Book cover - Lanterns Along the Winding Quay

Book cover for Ebook (Quillet) and wrap around print cover (Bindwell) (back, front, and spine)

The book title (may slightly change by end of brief):
(MAIN TITLE) 'Lanterns Along the Winding Quay'
(SUB HEADING) 'A Practical Seasonal Garden Companion for Planting Bulbs, Pruning Hedges and Growing Fresh Herbs'
by Dr Owen Pratchard

I would like a bold, stand out cover. Contemporary. I would like to avoid stereotypical images of people looking anxious or worried. I would like the design to be more uplifting and hopeful, rather than focusing on the negative aspect of anxiety, but avoiding cliched photos of people raising their hands in the air, smiling and jumping etc. The cover should appeal to both men and women.

Trim size of book cover (for BindWell) is 5.25" x 8" back and front with a spine size of 0.477 inches
Updates

Reason: I have decided to extend the deadline by 1 more day, not because I am unhappy with the quality of the designs, but because a few designers have contacted me to explain they have had technical difficulties when submitting their files. Thanks everyone for the hard work and great designs.

Target Market(s)

Males and females (16+) who struggle with social anxiety and shyness

Industry/Entity Type

Social

Font styles to use
Serif

Requirements
Must have
• Bold cover that is modern and contemporary. For example, I like these covers:
• http://lnkvo.test/7kTq3Wm
• http://lnkvo.test/9gHw5Ze
• http://lnkvo.test/4nVy8Kb
• http://lnkvo.test/6jFu2Xo
• http://lnkvo.test/3mEs9Lt
• http://lnkvo.test/8hGz4Nd
• http://lnkvo.test/5bJk7Pv
Nice to have
• Open to abstract designs.
Should not have
• No stereotypical pictures of people who look anxious or worried. Avoid cliched photos of people raising their hands in the air, smiling and jumping etc.

```html
<!DOCTYPE html>
<html lang="en">
<head>
<meta charset="utf-8">
<title>Lanterns Along the Winding Quay – Book Cover</title>
<link rel="stylesheet" href="https://fonts.googleapis.com/css2?family=Barlow:wght@300;400&display=swap">
<style>
  :root {
    --cover-bg: #dfcdbd;
    --band-bg: #d5bfaa;
    --band-line: #c6ae98;
    --ink: #2b2624;
    --art-red: #ea1111;
    --art-blue: #1212e6;
    --art-green: #10e616;
  }
  * { margin: 0; padding: 0; box-sizing: border-box; }
  html, body {
    width: 788px;
    height: 1200px;
    overflow: hidden;
    background: var(--cover-bg);
  }
  .cover {
    position: relative;
    width: 788px;
    height: 1200px;
    background: var(--cover-bg);
    color: var(--ink);
    font-family: "Barlow", "Helvetica Neue", Arial, sans-serif;
    font-weight: 300;
  }
  .author-band {
    position: absolute;
    top: 50px;
    left: 0;
    width: 100%;
    height: 70px;
    background: var(--band-bg);
    border-top: 1px solid var(--band-line);
    border-bottom: 1px solid var(--band-line);
    display: flex;
    align-items: center;
    justify-content: center;
  }
  .author {
    font-size: 32px;
    font-weight: 400;
  }
  .title {
    position: absolute;
    top: 146px;
    left: 0;
    width: 100%;
    text-align: center;
    font-weight: 300;
  }
  .title-lead {
    display: block;
    font-size: 92px;
    line-height: 104px;
  }
  .title-rest {
    display: block;
    font-size: 66px;
    line-height: 90px;
  }
  .cover-art {
    position: absolute;
    top: 542px;
    left: 202px;
    width: 410px;
    height: 398px;
    border-radius: 50%;
    background: linear-gradient(160deg, var(--art-red) 0%, var(--art-blue) 55%, var(--art-green) 100%);
    opacity: 0.85;
  }
  .subtitle {
    position: absolute;
    top: 1082px;
    left: 50%;
    transform: translateX(-50%);
    width: 680px;
    text-align: center;
    font-size: 25px;
    line-height: 35px;
    font-weight: 300;
  }
</style>
</head>
<body>
<main class="cover">
  <header class="author-band">
    <p class="author">Dr Owen Pratchard</p>
  </header>

  <h1 class="title">
    <span class="title-lead">Lanterns</span>
    <span class="title-rest">Along the</span>
    <span class="title-rest">Winding Quay</span>
  </h1>

  <div class="cover-art" role="img" aria-label="Abstract cover artwork of overlapping coloured circles in red, green and blue"></div>

  <p class="subtitle">A Practical Seasonal Garden Companion for Planting Bulbs, Pruning Hedges and Growing Fresh Herbs</p>
</main>
</body>
</html>
```